Summit Bodyform Gym Website

We need a website design for our gym.

Summit is the UAE's first calisthenics and parkour gym. The theme under which the gym revolves is that one does not require any machinery to workout as our bodies could be themselves the machinery. The gym is designed to be the more of a social hub rather than an "in-and-out" gym, where people come train, have fun, hang out and socialize for a few hours rather than just train for 60 minutes then leave. The gym is designed to be a big open space with lots of natural sunlight, natural wood and plants all over the place to create a natural and refreshing setting. We also use recycled material throughout the gym and recycle our waste as being green is part of our philosophy. We currently also have some of the world's top and most recognized calisthenics athletes working with us.

We would like our website to reflect all that as well as provide a simple, interactive and fun way for visitors to be able to get class and gym information, check out gym media and contact us for bookings.

Target Market(s)

Ages 15-35

Industry/Entity Type

Fitness

Coding

Coded - Design and coding required

Number of Pages Required

4 page

Font styles to use
Decorative

Colors
0792cd

Requirements
Must have
• Class descriptions
• Gym description
• Class schedules
• Trainer profiles
• Gym philosophy
• Contact Details
Nice to have
• A link to contact us directly for a free first trial class

```html
<!DOCTYPE html>
<html lang="en">
<head>
<meta charset="utf-8">
<title>Summit Bodyform Gym</title>
<link href="https://fonts.googleapis.com/css2?family=Roboto+Condensed:wght@400;700&family=Roboto:wght@400;500&display=swap" rel="stylesheet">
<style>
:root{
  --blue:#0792cd;
  --ink:#231f20;
  --dark:#1c1c1c;
  --grey-bg:#e9e9e9;
  --text:#333;
  --muted:#8a8a8a;
  --icon:#4a4a4a;
  --white:#fff;
}
*{margin:0;padding:0;box-sizing:border-box}
html,body{width:700px;height:1200px;overflow:hidden;background:var(--white)}
body{position:relative;font-family:"Roboto",sans-serif;color:var(--text)}
.abs{position:absolute}
.heading{font-family:"Roboto Condensed",sans-serif;font-weight:400}

/* hero */
.hero{left:0;top:0;width:700px;height:360px}
.brand{left:98px;top:16px;font-family:"Roboto Condensed",sans-serif;font-weight:700;font-size:22px;color:var(--ink);letter-spacing:.3px}
.brand-tag{left:100px;top:42px;font-family:"Roboto Condensed",sans-serif;font-size:7px;color:var(--ink)}
.nav{left:266px;top:36px;display:flex;gap:13px;font-size:7px;color:var(--white)}
.trial-title{left:480px;top:166px;font-family:"Roboto Condensed",sans-serif;font-size:14px;color:var(--white);transform:rotate(-12deg);transform-origin:left bottom;white-space:nowrap}
.field{left:480px;width:113px;height:19px;border:1px solid rgba(255,255,255,.25);font-size:5.5px;color:rgba(255,255,255,.55);padding:6px 7px}
.submit{left:480px;top:316px;font-family:"Roboto Condensed",sans-serif;font-weight:700;font-size:10px;color:var(--white);text-decoration:underline}
.dots{left:333px;top:334px;display:flex;gap:5px}
.dots span{width:5px;height:5px;border-radius:50%;background:var(--white)}
.dots span.on{background:transparent;border:1px solid var(--white)}

/* welcome */
.welcome-title{left:0;top:392px;width:700px;text-align:center;font-size:22px;color:var(--blue)}
.welcome-lead{left:0;top:424px;width:700px;text-align:center;font-family:"Roboto Condensed",sans-serif;font-size:8.6px;color:var(--ink)}
.welcome-body{left:77px;top:442px;width:546px;text-align:center;font-size:5.7px;line-height:11.7px;color:var(--muted)}
.btn{left:317px;top:497px;width:66px;height:26px;border:1px solid #cfcfcf;background:var(--white);font-size:7.5px;color:var(--text);text-align:center;line-height:24px}

/* description */
.desc-title{left:76px;top:560px;font-size:18px;color:var(--white)}
.card-photo{width:76px;height:76px;border:2px solid var(--white)}
.card-title{font-size:17px;color:var(--white)}
.card-text{width:168px;font-size:5.2px;line-height:10.4px;color:var(--white)}

/* philosophy */
.philosophy{left:0;top:731px;width:700px;height:112px;background:var(--grey-bg)}
.phil-title{left:0;top:757px;width:700px;text-align:center;font-size:20px;color:var(--text)}
.phil-text{left:80px;top:788px;width:540px;text-align:center;font-family:"Roboto Condensed",sans-serif;font-size:8.4px;line-height:13.6px;color:var(--ink)}

/* gallery */
.gallery-title{left:0;top:869px;width:700px;text-align:center;font-size:20px;color:var(--text)}
.gallery-photo{top:903px;width:173px;height:112px}
.gal-dots{left:319px;top:1041px;display:flex;gap:13px}
.gal-dots span{width:6px;height:6px;border-radius:50%;border:1px solid #ccc}
.gal-dots span.on{background:#ccc}

/* footer */
.social{top:1092px;width:22px;height:22px}
.footer-rule{left:77px;top:1132px;width:545px;height:1px;background:#444}
.footer-links{left:78px;top:1151px;font-size:6.2px;color:#9a9a9a;display:flex;gap:5px}
.copyright{left:78px;top:1166px;font-size:6.2px;color:#9a9a9a}
.footer-brand{left:588px;top:1150px;font-family:"Roboto Condensed",sans-serif;font-weight:700;font-size:10px;color:#6a6a6a}
</style>
</head>
<body>

<!-- hero -->
<svg class="abs hero" viewBox="0 0 700 360">
  <defs>
    <linearGradient id="heroPhoto" x1="0" y1="0" x2="1" y2="1">
      <stop offset="0" stop-color="#3a3530"/>
      <stop offset=".45" stop-color="#6b5a48"/>
      <stop offset="1" stop-color="#2c3a3f"/>
    </linearGradient>
  </defs>
  <rect width="700" height="360" fill="url(#heroPhoto)" role="img" aria-label="Athlete training on a bar in the gym"/>
  <path d="M180 38 L700 36 L700 0 L200 0 Z" fill="var(--blue)" opacity=".92"/>
  <path d="M0 0 L190 0 C190 30 185 80 150 82 C100 84 40 40 0 22 Z" fill="var(--white)"/>
  <path d="M470 165 L595 140 L618 305 L618 348 L470 348 Z" fill="rgba(20,20,20,.8)"/>
  <path d="M0 298 C120 310 260 352 390 350 C520 348 620 308 700 296 L700 360 L0 360 Z" fill="var(--blue)"/>
  <path d="M0 330 C120 340 250 360 370 357 C500 354 620 318 700 310 L700 360 L0 360 Z" fill="var(--white)"/>
</svg>
<div class="abs brand">Summit</div>
<div class="abs brand-tag">calisthenics gym</div>
<nav class="abs nav"><span>Home</span><span>Class descriptions</span><span>Gym description</span><span>Class schedules</span><span>Trainer profiles</span><span>Gym philosophy</span><span>Contact</span></nav>
<div class="abs trial-title">Free First Trial Class</div>
<div class="abs field" style="top:202px">Name</div>
<div class="abs field" style="top:230px">Email</div>
<div class="abs field" style="top:258px">Phone</div>
<div class="abs field" style="top:286px">Message</div>
<div class="abs submit">SUBMIT</div>
<div class="abs dots"><span class="on"></span><span></span><span></span><span></span></div>

<!-- welcome -->
<h1 class="abs heading welcome-title">Welcome to Summit Bodyform Gym</h1>
<p class="abs welcome-lead">Curabitur ac elit leo. In eleifend dui tellus, in scelerisque elit porttitor et. Integer eu massa lacinia, lacinia nulla non, volutpat purus.</p>
<p class="abs welcome-body">Aenean sed quam non sapien faucibus consequat vitae sit amet orci. Praesent quis risus mi. In mollis nulla in pulvinar dictum. Vivamus interdum sagittis felis, ut dapibus ligula feugiat ac. In dictum sapien eu tellus finibus fermentum. Aenean faucibus lacus ut mollis commodo. Donec vestibulum odio sem, ac laoreet massa ullamcorper id. Donec molestie nisi et tellus hendrerit vehicula. Nunc eu ligula sed quam pulvinar maximus in vitae eros. Proin porta fermentum ipsum, vel porttitor turpis venenatis luctus. Vivamus volutpat eu sapien quis tempus. Aenean feugiat viverra lorem ac sagittis. Donec sit amet lectus nec mi tempor laoreet ac nec nunc. Duis id auctor sapien.</p>

<!-- description band -->
<svg class="abs" style="left:0;top:470px" width="700" height="261" viewBox="0 0 700 261">
  <path d="M0 24 C90 20 150 75 230 100 C300 118 370 124 440 124 L440 128 C300 130 150 124 0 118 Z" fill="var(--ink)"/>
  <path d="M0 118 C150 124 300 130 440 126 C560 118 610 30 700 0 L700 261 L0 261 Z" fill="var(--blue)"/>
</svg>
<div class="abs btn">Know more</div>
<h2 class="abs heading desc-title">Description</h2>

<div class="abs card-photo" style="left:77px;top:623px;background:linear-gradient(180deg,#cfd6da,#4a4f52)" role="img" aria-label="Open gym floor with training rigs"></div>
<h3 class="abs heading card-title" style="left:161px;top:618px">Gym</h3>
<p class="abs card-text" style="left:161px;top:650px">Phasellus nisl est, condimentum vitae faucibus in, sollicitudin vel metus. Nunc sit amet consequat risus. Curabitur ac elit leo. In eleif end dui tellus, in scelerisque elit porttitor et. Integer eu massa lacin ia, lacinia nulla non, volutpat purus. Sed libero felis, vestibulum et dolor eget, lacinia aliquet neque.</p>

<div class="abs card-photo" style="left:371px;top:623px;background:linear-gradient(180deg,#5a6e7a,#1f2a30)" role="img" aria-label="Gymnastic rings hanging from a rig"></div>
<h3 class="abs heading card-title" style="left:455px;top:618px">Class</h3>
<p class="abs card-text" style="left:455px;top:650px">Phasellus nisl est, condimentum vitae faucibus in, sollicitudin vel metus. Nunc sit amet consequat risus. Curabitur ac elit leo. In eleif end dui tellus, in scelerisque elit porttitor et. Integer eu massa lacin ia, lacinia nulla non, volutpat purus. Sed libero felis, vestibulum et dolor eget, lacinia aliquet neque.</p>

<!-- philosophy -->
<section class="abs philosophy"></section>
<h2 class="abs heading phil-title">Our Philosophy</h2>
<p class="abs phil-text">Donec vestibulum odio sem, ac laoreet massa ullamcorper id. Donec molestie nisi et tellus hendrerit vehicula. Nunc eu ligula sed quam pulvinar maximus in vitae. Proin porta fermentum ipsum, vel porttitor turpis venenatis luctus.</p>

<!-- gallery -->
<h2 class="abs heading gallery-title">Gallery</h2>
<div class="abs gallery-photo" style="left:78px;background:linear-gradient(180deg,#a08058,#8a3a2c)" role="img" aria-label="Weights area with a planted wall"></div>
<div class="abs gallery-photo" style="left:263px;background:linear-gradient(180deg,#7a8890,#8c3e2e 70%,#6fc3e0)" role="img" aria-label="Studio room with blue mats"></div>
<div class="abs gallery-photo" style="left:449px;background:linear-gradient(180deg,#c8ccd0,#3a3c40)" role="img" aria-label="Main training hall with rigs"></div>
<div class="abs gal-dots"><span class="on"></span><span></span><span></span><span></span></div>

<!-- footer -->
<svg class="abs" style="left:0;top:1070px" width="700" height="130" viewBox="0 0 700 130">
  <path d="M0 48 C140 20 250 4 350 4 C480 4 600 24 700 36 L700 130 L0 130 Z" fill="var(--dark)"/>
</svg>
<svg class="abs social" style="left:296px" viewBox="0 0 22 22" aria-label="Website">
  <circle cx="11" cy="11" r="11" fill="#fff"/>
  <g fill="none" stroke="var(--icon)" stroke-width=".9">
    <circle cx="11" cy="11" r="5"/>
    <ellipse cx="11" cy="11" rx="2.2" ry="5"/>
    <path d="M6 11 H16"/>
  </g>
</svg>
<svg class="abs social" style="left:325px" viewBox="0 0 22 22" aria-label="Chat">
  <circle cx="11" cy="11" r="11" fill="#fff"/>
  <path d="M6 7 H16 V13.5 H10 L7.5 16 V13.5 H6 Z" fill="var(--icon)"/>
</svg>
<svg class="abs social" style="left:353px" viewBox="0 0 22 22" aria-label="Share">
  <circle cx="11" cy="11" r="11" fill="#fff"/>
  <path d="M8 11 L14 7.5 M8 11 L14 14.5" stroke="var(--icon)" stroke-width=".9"/>
  <circle cx="8" cy="11" r="1.7" fill="var(--icon)"/>
  <circle cx="14" cy="7.5" r="1.7" fill="var(--icon)"/>
  <circle cx="14" cy="14.5" r="1.7" fill="var(--icon)"/>
</svg>
<svg class="abs social" style="left:380px" viewBox="0 0 22 22" aria-label="Email">
  <circle cx="11" cy="11" r="11" fill="#fff"/>
  <rect x="6" y="7.5" width="10" height="7" rx="1" fill="var(--icon)"/>
  <path d="M6.5 8 L11 11.5 L15.5 8" fill="none" stroke="#fff" stroke-width=".9"/>
</svg>
<div class="abs footer-rule"></div>
<nav class="abs footer-links"><span>Home</span><span>|</span><span>Class descriptions</span><span>|</span><span>Gym description</span><span>|</span><span>Class schedules</span><span>|</span><span>Trainer profiles</span><span>|</span><span>Gym philosophy</span><span>|</span><span>Contact</span></nav>
<p class="abs copyright">Copyright &copy; 2015 Summit. All rights reserved.</p>
<div class="abs footer-brand">Summit</div>

</body>
</html>
```